Natural healthcare clinic needs stationery and business card design

We have had a logo developed by Pixel Harbor and are now looking at utilising it for a new business concept. The concept is a natural healthcare clinic that hosts a number of small businesses. The individual practitioners may want to utilise the host business stationery to provide a consistent message to clients.

I am looking for a stationery design - letterhead, DL brochure template and business card that uses our logo. The business name 'Bright Meadows' is all about getting rhythm back into your life so you can be fit and healthy. The stationery design should reflect this.

There are a couple of requirements for the business card, it needs to be double-sided with black and white back. There should be lines to write appointment times on. The cards may need to be custom named on the front for example Carol Fenwick, Remedial Therapist and Aromatherapist. Therefore if a template can be provided so we can customise this information using MS Publisher, it would be appreciated.

The DL brochure template needs to be A4 folded to DL. I am looking for a consistent brand message that can be utilised to produce our own clinic brochures.

The natural healthcare clinic will host the following types of businesses - remedial massage, pregnancy massage, oncology massage, aromatherapy, acupuncture - as a bit of a guide.

Target Market(s)

25-45 year old male and females who work full time.

Industry/Entity Type

Healthcare

Requirements
Must have
• Use the logo I have already.

```html
<!DOCTYPE html>
<html lang="en">
<head>
<meta charset="utf-8">
<title>Bright Meadows Letterhead</title>
<link href="https://fonts.googleapis.com/css2?family=Open+Sans:wght@400;600&display=swap" rel="stylesheet">
<style>
  :root {
    --backdrop: #e9e4dc;
    --paper: #ffffff;
    --brand-green: #7a9a1f;
    --brand-green-light: #a6c634;
    --brand-green-dark: #5d7c14;
    --accent-peach: #f7b98a;
    --text-dark: #3a3a3a;
    --icon-orange: #e8792b;
  }
  * { margin: 0; padding: 0; box-sizing: border-box; }
  html, body {
    width: 1200px;
    height: 1024px;
    overflow: hidden;
    background: var(--backdrop);
    font-family: "Open Sans", Arial, sans-serif;
  }
  .letterhead {
    position: absolute;
    left: 253px;
    top: 22px;
    width: 694px;
    height: 980px;
    background: var(--paper);
    box-shadow: 0 6px 18px rgba(0,0,0,0.18);
    overflow: hidden;
  }
  .brand {
    position: absolute;
    left: 56px;
    top: 90px;
    display: flex;
    align-items: center;
    gap: 12px;
    font-size: 30px;
    font-weight: 400;
    color: var(--brand-green);
    letter-spacing: 0.5px;
  }
  .brand-dot {
    width: 22px;
    height: 22px;
    border-radius: 50%;
    background: var(--brand-green);
  }
  .contact {
    position: absolute;
    right: 40px;
    top: 120px;
    width: 210px;
    font-size: 11px;
    font-style: normal;
    line-height: 1.45;
    color: var(--text-dark);
  }
  .contact-address { margin-bottom: 4px; }
  .contact-line { display: flex; align-items: center; gap: 6px; }
  .contact-line svg { width: 10px; height: 10px; flex: none; }
  .footer-band {
    position: absolute;
    left: 0;
    bottom: 0;
    width: 694px;
    height: 230px;
  }
  .website {
    position: absolute;
    left: 60px;
    bottom: 52px;
    font-size: 13px;
    color: #ffffff;
    letter-spacing: 0.3px;
  }
</style>
</head>
<body>
  <main class="letterhead">
    <header class="brand">
      <span class="brand-dot"></span>
      <span class="brand-name">Bright Meadows</span>
    </header>

    <address class="contact">
      <p class="contact-address">18 Fernbank Lane, Millbrook,<br>4021, Australia</p>
      <p class="contact-line">
        <svg viewBox="0 0 10 10" aria-hidden="true"><path d="M2 1 L4 1 L5 3 L4 4 Q5 6 6 6 L7 5 L9 6 L9 8 Q8 9 7 9 Q1 8 1 2 Q1 1 2 1 Z" fill="var(--icon-orange)"/></svg>
        415-220-7341
      </p>
      <p class="contact-line">
        <svg viewBox="0 0 10 10" aria-hidden="true"><rect x="1" y="3" width="8" height="5" rx="1" fill="var(--icon-orange)"/><rect x="3" y="1" width="4" height="3" fill="var(--icon-orange)"/></svg>
        415-220-7390
      </p>
      <p class="contact-line">
        <svg viewBox="0 0 10 10" aria-hidden="true"><rect x="1" y="2" width="8" height="6" fill="var(--icon-orange)"/><path d="M1 2 L5 6 L9 2" stroke="#fff" stroke-width="0.8" fill="none"/></svg>
        hello@brightmeadows.com
      </p>
    </address>

    <svg class="footer-band" viewBox="0 0 694 230" preserveAspectRatio="none" aria-hidden="true">
      <defs>
        <linearGradient id="bandGradient" x1="0" y1="0" x2="1" y2="0">
          <stop offset="0" stop-color="var(--brand-green-dark)"/>
          <stop offset="0.45" stop-color="var(--brand-green-light)"/>
          <stop offset="1" stop-color="var(--brand-green)"/>
        </linearGradient>
      </defs>
      <path d="M0 12 C160 40 320 120 460 160 C560 185 640 180 694 170 L694 230 L0 230 Z" fill="var(--accent-peach)"/>
      <path d="M0 26 C160 56 320 134 460 172 C560 196 640 192 694 182 L694 230 L0 230 Z" fill="#ffffff"/>
      <path d="M0 34 C160 64 320 142 460 180 C560 204 640 200 694 190 L694 230 L0 230 Z" fill="url(#bandGradient)"/>
    </svg>
    <p class="website">www.brightmeadows.com</p>
  </main>
</body>
</html>
```